Dental Practice Billboard Design

We are a newer dental practice in need of a simple but appealing billboard for our growing dental practice to attract new patients. The practice is owned by husband and wife dentists and is family friendly in a small town in Kentucky. We try to be very friendly and caring to our patients. Would prefer a blue background for the billboard and our tooth logo to be prominent. We are partial to the Patua One font used in the image below but please feel free to tweak it as you deem necessary. The shape of the uppercase D and lowercase g are why we like that font, so fonts with a similarly shaped “D” and “g” would work as well. Please include our phone number (555) 847-1390. Please see our website Harlowbrookdentistry.example for more info on the practice if needed. Thank you! Looking forward to seeing your creation.
Updates

The dimensions will be 12ft x 24ft (3.6576m x 7.3152m). Apologies for not including this in the original prompt. Thank you all for your submissions.

Industry/Entity Type

Dental

Font styles to use
Other font styles liked:
• Patua One

Colors
0054AA
0677BA
7BADD7
CADEEF
E8F1F8
0094D4
00A9DD
6FCCEA
C7EBF8
E9F6FB
00AB8E
00BBA5
67D7C9
C6EFE9
E9F9F6
59FF00
82FF00
B8FF75
E3FFCB
F4FFEA

Requirements
Must have
• Phone number, website, Logo, Practice name “Harlow Brook Dentistry”
Should not have
• A tagline or slogan

```html
<!DOCTYPE html>
<html lang="en">
<head>
<meta charset="utf-8">
<title>Harlow Brook Dentistry Billboard</title>
<link href="https://fonts.googleapis.com/css2?family=Patua+One&family=Fira+Sans:wght@600&display=swap" rel="stylesheet">
<style>
  :root {
    --brand-blue: #1e56a6;
    --brand-green: #22a84a;
    --board-white: #ffffff;
    --backdrop: #0094d4;
    --backdrop-light: #6fccea;
  }
  * { margin: 0; padding: 0; box-sizing: border-box; }
  html, body {
    width: 1200px;
    height: 886px;
    overflow: hidden;
    background: linear-gradient(180deg, var(--backdrop-light) 0%, var(--backdrop) 100%);
  }
  .billboard {
    position: absolute;
    left: 30px;
    top: 158px;
    width: 1140px;
    height: 570px;
    background: var(--board-white);
    overflow: hidden;
    box-shadow: 0 8px 28px rgba(0, 40, 90, 0.3);
  }
  .corner-bands {
    position: absolute;
    inset: 0;
    width: 100%;
    height: 100%;
  }
  .logo-mark {
    position: absolute;
    left: 60px;
    top: 120px;
    width: 290px;
    display: flex;
    flex-direction: column;
    align-items: center;
    gap: 22px;
  }
  .logo-mark .dot {
    width: 170px;
    height: 170px;
    border-radius: 50%;
    background: var(--brand-green);
  }
  .logo-mark .logo-name {
    font-family: "Patua One", serif;
    font-size: 50px;
    line-height: 1.05;
    text-align: center;
    color: var(--brand-blue);
  }
  .practice-name {
    position: absolute;
    left: 380px;
    top: 70px;
    font-family: "Patua One", serif;
    font-weight: 400;
    color: var(--brand-blue);
    letter-spacing: 0.04em;
  }
  .practice-name .primary {
    display: block;
    font-size: 128px;
    line-height: 1;
  }
  .practice-name .secondary {
    display: block;
    font-size: 54px;
    line-height: 1.1;
    margin-top: 4px;
  }
  .website {
    position: absolute;
    left: 380px;
    top: 300px;
    width: 690px;
    height: 82px;
    background: var(--brand-blue);
    color: var(--board-white);
    font-family: "Patua One", serif;
    font-size: 44px;
    line-height: 82px;
    padding-left: 16px;
    white-space: nowrap;
  }
  .phone {
    position: absolute;
    left: 380px;
    top: 388px;
    font-family: "Fira Sans", sans-serif;
    font-weight: 600;
    font-size: 98px;
    line-height: 1.1;
    color: var(--brand-green);
    white-space: nowrap;
  }
</style>
</head>
<body>
  <main class="billboard">
    <svg class="corner-bands" viewBox="0 0 1140 570" preserveAspectRatio="none" aria-hidden="true">
      <polygon points="720,70 1140,0 1140,70" fill="var(--brand-blue)"/>
      <polygon points="560,92 1140,68 1140,78" fill="var(--brand-green)"/>
      <polygon points="0,490 420,515 0,570" fill="var(--brand-blue)"/>
      <polygon points="0,478 560,510 0,500" fill="var(--brand-green)"/>
      <polygon points="0,500 560,510 420,516 0,492" fill="var(--brand-blue)"/>
    </svg>

    <div class="logo-mark">
      <span class="dot"></span>
      <span class="logo-name">Harlow<br>Brook</span>
    </div>

    <h1 class="practice-name">
      <span class="primary">HARLOW</span>
      <span class="secondary">BROOK DENTISTRY</span>
    </h1>

    <p class="website">Harlowbrookdentistry.example</p>

    <p class="phone">(555) 847-1390</p>
  </main>
</body>
</html>
```